Business Card for Coastal Tundrabridge Advisory

We need a business card for Coastal Tundrabridge Advisory. The company website address is provided below. The company logo is attached. We provide specialized permafrost services to the mining, transportation, and oil & gas industries. The card should be prepared for:
Matthias Korhonen, PhD.
Coastal Tundrabridge Advisory
PO Box 418259
Quillwater, Alaska 99642
Direct: +1-907-555-0143
Email: mkorhonen@tundrabridgeadvisory.example
Website: www.coastaltundrabridgeadvisory.example

```html
<!DOCTYPE html>
<html lang="en">
<head>
<meta charset="utf-8">
<title>Coastal Tundrabridge Advisory – Business Card</title>
<link href="https://fonts.googleapis.com/css2?family=Arimo:wght@400;700&family=Roboto+Condensed:wght@700&display=swap" rel="stylesheet">
<style>
  :root {
    --backdrop: #d9dadc;
    --card: #f7f7f7;
    --card-edge: #e6e6e6;
    --ink: #1b2129;
    --band: #1e252e;
    --muted: #55595e;
    --on-band: #ffffff;
  }
  * { margin: 0; padding: 0; box-sizing: border-box; }
  html, body { width: 1200px; height: 900px; overflow: hidden; }
  body {
    background: var(--backdrop);
    font-family: "Arimo", Arial, sans-serif;
    color: var(--ink);
    position: relative;
  }
  .card {
    position: absolute;
    left: 280px;
    width: 640px;
    height: 366px;
    background: linear-gradient(135deg, #ffffff 0%, var(--card) 60%, var(--card-edge) 100%);
    border-radius: 4px;
    box-shadow: 0 10px 24px rgba(0,0,0,0.22);
    overflow: hidden;
  }
  .card--front { top: 64px; }
  .card--back { top: 470px; }
  .band { position: absolute; left: 0; bottom: 0; width: 640px; }
  .card--front .band { height: 110px; }
  .card--back .band { height: 74px; }
  .tagline {
    position: absolute; left: 40px; top: 42px; width: 340px;
    font-size: 15px; line-height: 1.3; color: var(--ink);
  }
  .brand {
    position: absolute;
    font-family: "Arimo", Arial, sans-serif;
    font-weight: 700;
    color: var(--ink);
    text-transform: uppercase;
    letter-spacing: 1px;
    text-align: right;
    line-height: 1.1;
  }
  .card--front .brand { right: 36px; top: 138px; font-size: 24px; }
  .card--back .brand { right: 36px; top: 40px; font-size: 24px; }
  .web {
    position: absolute;
    color: var(--on-band);
    font-size: 14px;
    letter-spacing: 0.2px;
    white-space: nowrap;
  }
  .card--front .web { left: 38px; bottom: 28px; }
  .card--back .web { right: 28px; bottom: 36px; }
  .contact { position: absolute; left: 44px; top: 120px; }
  .contact__name {
    font-family: "Roboto Condensed", "Arial Narrow", sans-serif;
    font-weight: 700; font-size: 19px; text-transform: uppercase; color: var(--ink);
  }
  .contact__name span { text-transform: none; }
  .contact__company { font-size: 15px; color: var(--muted); margin-top: 2px; }
  .contact__address { font-size: 15px; color: var(--muted); margin: 20px 0 0 24px; line-height: 1.3; }
  .contact__lines { margin: 14px 0 0 24px; font-size: 14px; color: var(--muted); }
  .contact__line { display: flex; align-items: center; gap: 8px; line-height: 1.45; white-space: nowrap; }
  .contact__line svg { width: 14px; height: 14px; flex: none; }
</style>
</head>
<body>

<section class="card card--front" aria-label="Card front">
  <p class="tagline">We Provide Specialized Permafrost Services To The Mining, Transportation, And Oil &amp; Gas Industries</p>
  <div class="brand">Coastal Tundrabridge<br>Advisory</div>
  <svg class="band" viewBox="0 0 640 110" aria-hidden="true">
    <path fill="var(--band)" d="M0 44 H305 Q320 44 330 52 L352 72 Q358 78 368 78 H640 V110 H0 Z"/>
  </svg>
  <span class="web">coastaltundrabridgeadvisory.example</span>
</section>

<section class="card card--back" aria-label="Card back">
  <div class="brand">Coastal Tundrabridge<br>Advisory</div>
  <div class="contact">
    <div class="contact__name">Matthias Korhonen, <span>PhD.</span></div>
    <div class="contact__company">Coastal Tundrabridge Advisory</div>
    <div class="contact__address">PO Box 418259<br>Quillwater, Alaska 99642</div>
    <div class="contact__lines">
      <div class="contact__line">
        <svg viewBox="0 0 24 24" aria-hidden="true"><path fill="var(--ink)" d="M6.6 10.8a15.1 15.1 0 0 0 6.6 6.6l2.2-2.2c.3-.3.7-.4 1-.2 1.1.4 2.3.6 3.6.6.6 0 1 .4 1 1V20c0 .6-.4 1-1 1A17 17 0 0 1 3 4c0-.6.4-1 1-1h3.5c.6 0 1 .4 1 1 0 1.3.2 2.5.6 3.6.1.3 0 .7-.2 1z"/></svg>
        <span>+1-907-555-0143</span>
      </div>
      <div class="contact__line">
        <svg viewBox="0 0 24 24" aria-hidden="true"><path fill="var(--ink)" d="M2 5h20v14H2z"/><path fill="none" stroke="#fff" stroke-width="1.6" d="M2.5 5.5 12 13l9.5-7.5"/></svg>
        <span>mkorhonen@tundrabridgeadvisory.example</span>
      </div>
    </div>
  </div>
  <svg class="band" viewBox="0 0 640 74" aria-hidden="true">
    <path fill="var(--band)" d="M640 0 H352 Q340 0 340 12 V48 Q340 54 346 57 L360 64 H0 V74 H640 Z"/>
  </svg>
  <span class="web">coastaltundrabridgeadvisory.example</span>
</section>

</body>
</html>
```